Mission Statement Board for front lobby

We need a mission statement board for our front lobby at our company called TrellisWorks. We are a web content management company that builds websites for our clients. We would like two boards, same size, canvas material (not thin poster board or anything like that) size H 3' x L 2', white background, blue and black colored font, our logo on top in blue/gray/black and some blue coloring around top and bottom, kind of framing the white background. Please reference our very rough draft we did in Word so you get an idea of what we're thinking- the attachment shows what we would like on each board. Reference our website to see logo and fonts if you would like, please keep the board similar to our fonts and colors. www.trellisworks-example.com

Contact info: Marta Kowalczyk
Email: marta.kowalczyk@trellisworks-example.com
Phone: 555-207-3948
Updates

Please do not include in a design my contact info, no email marta.kowalczyk@trellisworks-example.com, no phone # 555-207-3948. I added that info to the project when I posted it, but it is not part of the design.... reference attachment posted in project with exactly what we want.

Target Market(s)

Clients & employees in the office who will see the boards in lobby

Industry/Entity Type

It Company

Font styles to use
Other font styles liked:
• reference attachment (but font is flexible within reason)

Colors
33a6d7
0255a3
eaf1f7
0292cd
85cae6
cee9f5
000000
5c5c5c
959595

Requirements
Must have
• Needs to be a professional sign that hangs on wall, company logo, cohesive colors and fonts
Nice to have
• Get creative with the border/framing around the white background
Should not have
• Unprofessional fonts, typos, thin cheap looking poster board materal.

```html
<!DOCTYPE html>
<html lang="en">
<head>
<meta charset="utf-8">
<title>TrellisWorks Lobby Boards</title>
<link href="https://fonts.googleapis.com/css2?family=Montserrat:wght@600;700&family=Open+Sans:wght@400;600&display=swap" rel="stylesheet">
<style>
  :root{
    --blue-deep:#0255a3;
    --blue-mid:#0292cd;
    --blue-bright:#33a6d7;
    --blue-soft:#85cae6;
    --blue-pale:#cee9f5;
    --blue-mist:#eaf1f7;
    --heading:#1c4176;
    --black:#000000;
    --charcoal:#333638;
    --gray-dark:#5c5c5c;
    --gray:#959595;
    --silver:#c4c7ca;
    --text:#3a3d40;
    --board:#f7f7f6;
    --backdrop:#eceae6;
    --divider:#3a3a3a;
  }
  *{box-sizing:border-box;margin:0;padding:0}
  html,body{width:1200px;height:1040px;overflow:hidden;background:var(--divider)}
  .sheet{display:grid;grid-template-columns:598px 598px;grid-template-rows:518px 518px;gap:4px;width:1200px;height:1040px}
  .option{background:var(--backdrop);display:flex;justify-content:center;align-items:center;gap:28px}
  .board{position:relative;width:214px;height:322px;background:var(--board);overflow:hidden;font-family:"Open Sans",Arial,sans-serif;color:var(--text)}
  .board-frame{position:absolute;inset:0;width:100%;height:100%}
  .board-content{position:absolute;left:18px;right:18px;top:44px;text-align:center}
  .brand{display:flex;align-items:center;justify-content:center;gap:5px;margin-bottom:22px}
  .brand-dot{width:9px;height:9px;border-radius:50%;background:var(--blue-deep)}
  .brand-name{font-family:"Montserrat",Arial,sans-serif;font-weight:700;font-size:11px;letter-spacing:.5px;color:var(--blue-deep)}
  .heading{font-family:"Montserrat",Arial,sans-serif;font-weight:700;font-size:12px;color:var(--heading);margin-bottom:5px}
  .statement{font-size:8.2px;line-height:1.45;margin-bottom:18px}
  .values-heading{margin-bottom:9px}
  .value{margin-bottom:7px;font-size:5.4px;line-height:1.4}
  .value-name{display:block;font-family:"Montserrat",Arial,sans-serif;font-weight:700;font-size:6.6px;color:var(--charcoal);letter-spacing:.2px}
  .values-inline{text-align:left}
  .values-inline .values-heading{text-align:center}
  .values-inline .value{text-align:justify;margin-bottom:6px}
  .values-inline .value-name{display:inline;margin-right:3px}
  .is-left .board-content{text-align:left}
  .is-left .brand{justify-content:flex-start;margin-left:6px}
  .is-left .statement{text-align:justify}
  .dots{position:absolute;right:16px;bottom:40px;display:flex;gap:3px}
  .dots span{width:6px;height:6px;border-radius:50%;background:var(--blue-deep)}
  .option-swoosh .board{background:linear-gradient(180deg,#f1f1f0,#e4e5e6 70%,#eeeeed)}
  .option-swoosh .board-content{top:70px}
  .option-swoosh .brand{margin-bottom:18px}
  .option-swoosh .statement{margin-bottom:14px}
  .option-bands .board-content{top:50px}
  .option-angles .board-content{top:42px}
  .option-wave .board-content{top:52px}
</style>
</head>
<body>
<main class="sheet">

  <section class="option option-swoosh">
    <article class="board">
      <svg class="board-frame" viewBox="0 0 220 330" preserveAspectRatio="none" aria-hidden="true">
        <path d="M0 0H220V8C120 8 30 22 0 80Z" fill="var(--blue-deep)"/>
        <path d="M130 0H220V8C190 8 160 10 130 14Z" fill="var(--silver)"/>
        <path d="M30 44C80 16 160 8 220 8V17C160 18 90 26 40 54Z" fill="var(--gray)"/>
        <path d="M0 94C14 42 90 22 220 20V28C100 32 26 52 0 108Z" fill="var(--charcoal)"/>
        <path d="M0 270C80 296 150 292 220 244V256C150 302 80 306 0 290Z" fill="var(--silver)"/>
        <path d="M0 296C70 312 150 306 220 258V270C150 318 70 322 0 308Z" fill="var(--gray)"/>
        <path d="M80 330C150 312 200 272 220 226V252C200 292 170 316 130 330Z" fill="var(--charcoal)"/>
        <path d="M130 330C180 312 205 292 220 262V330Z" fill="var(--blue-deep)"/>
        <path d="M0 316C40 318 80 320 110 330H0Z" fill="var(--blue-bright)"/>
      </svg>
      <div class="board-content">
        <div class="brand"><span class="brand-dot"></span><span class="brand-name">TRELLISWORKS</span></div>
        <h2 class="heading">OUR MISSION STATEMENT:</h2>
        <p class="statement">We design and implement extraordinary web solutions to help our clients achieve their goals.</p>
        <h2 class="heading">OUR FAITH...</h2>
        <p class="statement">We reflect the love of Christ in us and through us to our fellow employees, partners and clients.</p>
      </div>
    </article>
    <article class="board">
      <svg class="board-frame" viewBox="0 0 220 330" preserveAspectRatio="none" aria-hidden="true">
        <path d="M0 0H220V8C120 8 30 22 0 80Z" fill="var(--blue-deep)"/>
        <path d="M130 0H220V8C190 8 160 10 130 14Z" fill="var(--silver)"/>
        <path d="M30 44C80 16 160 8 220 8V17C160 18 90 26 40 54Z" fill="var(--gray)"/>
        <path d="M0 94C14 42 90 22 220 20V28C100 32 26 52 0 108Z" fill="var(--charcoal)"/>
        <path d="M0 270C80 296 150 292 220 244V256C150 302 80 306 0 290Z" fill="var(--silver)"/>
        <path d="M0 296C70 312 150 306 220 258V270C150 318 70 322 0 308Z" fill="var(--gray)"/>
        <path d="M80 330C150 312 200 272 220 226V252C200 292 170 316 130 330Z" fill="var(--charcoal)"/>
        <path d="M130 330C180 312 205 292 220 262V330Z" fill="var(--blue-deep)"/>
        <path d="M0 316C40 318 80 320 110 330H0Z" fill="var(--blue-bright)"/>
      </svg>
      <div class="board-content values-inline">
        <div class="brand"><span class="brand-dot"></span><span class="brand-name">TRELLISWORKS</span></div>
        <h2 class="heading values-heading">OUR CORE VALUES</h2>
        <p class="value"><span class="value-name">INTEGRITY -</span>We believe that to be successful, it is essential to operate at the highest levels of honesty, responsibility and trust.</p>
        <p class="value"><span class="value-name">ACCOUNTABILITY -</span>Taking responsibility for one's own actions.</p>
        <p class="value"><span class="value-name">RESPECT -</span>Understand and value differences in others. Listen thoughtfully to understand.</p>
        <p class="value"><span class="value-name">EXCELLENCE -</span>We continually improve our standards and processes so that excellence simply becomes a natural consequence of our work.</p>
        <p class="value"><span class="value-name">LOYALTY -</span>Working collaboratively with TrellisWorks employees, partners and customers to solve problems and achieve goals.</p>
      </div>
    </article>
  </section>

  <section class="option option-bands">
    <article class="board">
      <svg class="board-frame" viewBox="0 0 220 330" preserveAspectRatio="none" aria-hidden="true">
        <path d="M0 0H220V44L0 34Z" fill="var(--gray-dark)"/>
        <path d="M0 0H220V36L0 12Z" fill="var(--charcoal)"/>
        <path d="M60 0H220V38L90 18Z" fill="var(--blue-deep)"/>
        <path d="M0 288L220 298V330H0Z" fill="var(--gray-dark)"/>
        <path d="M0 294L220 306V330H0Z" fill="var(--charcoal)"/>
        <path d="M0 302L220 316V330H0Z" fill="var(--blue-deep)"/>
      </svg>
      <div class="board-content">
        <div class="brand"><span class="brand-dot"></span><span class="brand-name">TRELLISWORKS</span></div>
        <h2 class="heading">OUR MISSION STATEMENT:</h2>
        <p class="statement">We design and implement extraordinary web solutions to help our clients achieve their goals.</p>
        <h2 class="heading">OUR FAITH...</h2>
        <p class="statement">We reflect the love of Christ in us and through us to our fellow employees, partners and clients.</p>
      </div>
    </article>
    <article class="board">
      <svg class="board-frame" viewBox="0 0 220 330" preserveAspectRatio="none" aria-hidden="true">
        <path d="M0 0H220V44L0 34Z" fill="var(--gray-dark)"/>
        <path d="M0 0H220V36L0 12Z" fill="var(--charcoal)"/>
        <path d="M60 0H220V38L90 18Z" fill="var(--blue-deep)"/>
        <path d="M0 288L220 298V330H0Z" fill="var(--gray-dark)"/>
        <path d="M0 294L220 306V330H0Z" fill="var(--charcoal)"/>
        <path d="M0 302L220 316V330H0Z" fill="var(--blue-deep)"/>
      </svg>
      <div class="board-content">
        <div class="brand"><span class="brand-dot"></span><span class="brand-name">TRELLISWORKS</span></div>
        <h2 class="heading values-heading">OUR CORE VALUES</h2>
        <p class="value"><span class="value-name">INTEGRITY</span>We believe that to be successful, it is essential to operate at the highest levels of honesty, responsibility and trust.</p>
        <p class="value"><span class="value-name">ACCOUNTABILITY</span>Taking responsibility for one's own actions.</p>
        <p class="value"><span class="value-name">RESPECT</span>Understand and value differences in others. Listen thoughtfully to understand.</p>
        <p class="value"><span class="value-name">EXCELLENCE</span>We continually improve our standards and processes so that excellence simply becomes a natural consequence of our work.</p>
        <p class="value"><span class="value-name">LOYALTY</span>Working collaboratively with TrellisWorks employees, partners and customers to solve problems and achieve goals.</p>
      </div>
    </article>
  </section>

  <section class="option option-angles is-left">
    <article class="board">
      <svg class="board-frame" viewBox="0 0 220 330" preserveAspectRatio="none" aria-hidden="true">
        <path d="M0 0H220V4L0 46Z" fill="var(--charcoal)"/>
        <path d="M70 30L220 4V40Z" fill="var(--blue-mid)"/>
        <path d="M120 0H220V30Z" fill="var(--blue-deep)"/>
        <path d="M0 268L150 300V330H0Z" fill="var(--blue-mid)"/>
        <path d="M0 286L120 330H0Z" fill="var(--blue-deep)"/>
        <path d="M90 330L220 282V330Z" fill="var(--charcoal)"/>
      </svg>
      <div class="board-content">
        <div class="brand"><span class="brand-dot"></span><span class="brand-name">TRELLISWORKS</span></div>
        <h2 class="heading">OUR MISSION STATEMENT:</h2>
        <p class="statement">We design and implement extraordinary web solutions to help our clients achieve their goals.</p>
        <h2 class="heading">OUR FAITH...</h2>
        <p class="statement">We reflect the love of Christ in us and through us to our fellow employees, partners and clients.</p>
      </div>
      <div class="dots"><span></span><span></span><span></span></div>
    </article>
    <article class="board">
      <svg class="board-frame" viewBox="0 0 220 330" preserveAspectRatio="none" aria-hidden="true">
        <path d="M0 0H220V4L0 46Z" fill="var(--charcoal)"/>
        <path d="M70 30L220 4V40Z" fill="var(--blue-mid)"/>
        <path d="M120 0H220V30Z" fill="var(--blue-deep)"/>
        <path d="M0 268L150 300V330H0Z" fill="var(--blue-mid)"/>
        <path d="M0 286L120 330H0Z" fill="var(--blue-deep)"/>
        <path d="M90 330L220 282V330Z" fill="var(--charcoal)"/>
      </svg>
      <div class="board-content">
        <div class="brand"><span class="brand-dot"></span><span class="brand-name">TRELLISWORKS</span></div>
        <h2 class="heading values-heading">OUR CORE VALUES</h2>
        <p class="value"><span class="value-name">INTEGRITY</span>We believe that to be successful, it is essential to operate at the highest levels of honesty, responsibility and trust.</p>
        <p class="value"><span class="value-name">ACCOUNTABILITY</span>Taking responsibility for one's own actions.</p>
        <p class="value"><span class="value-name">RESPECT</span>Understand and value differences in others. Listen thoughtfully to understand.</p>
        <p class="value"><span class="value-name">EXCELLENCE</span>We continually improve our standards and processes so that excellence simply becomes a natural consequence of our work.</p>
        <p class="value"><span class="value-name">LOYALTY</span>Working collaboratively with TrellisWorks employees, partners and customers to solve problems and achieve goals.</p>
      </div>
      <div class="dots"><span></span><span></span><span></span></div>
    </article>
  </section>

  <section class="option option-wave">
    <article class="board">
      <svg class="board-frame" viewBox="0 0 220 330" preserveAspectRatio="none" aria-hidden="true">
        <path d="M0 0H220V48C150 18 70 18 0 48Z" fill="var(--blue-deep)"/>
        <path d="M0 18C70 4 150 4 220 22V36C150 14 70 14 0 34Z" fill="var(--blue-soft)" opacity=".7"/>
        <path d="M0 54C70 24 150 24 220 54" fill="none" stroke="var(--silver)" stroke-width="7"/>
        <path d="M0 60C70 32 150 32 220 60" fill="none" stroke="var(--blue-pale)" stroke-width="2"/>
        <path d="M0 282C70 308 150 308 220 282V330H0Z" fill="var(--blue-deep)"/>
        <path d="M0 300C70 318 150 318 220 296V312C150 330 70 330 0 314Z" fill="var(--blue-soft)" opacity=".7"/>
        <path d="M0 276C70 302 150 302 220 276" fill="none" stroke="var(--silver)" stroke-width="7"/>
        <path d="M0 270C70 294 150 294 220 270" fill="none" stroke="var(--blue-pale)" stroke-width="2"/>
      </svg>
      <div class="board-content">
        <div class="brand"><span class="brand-dot"></span><span class="brand-name">TRELLISWORKS</span></div>
        <h2 class="heading">OUR MISSION STATEMENT:</h2>
        <p class="statement">We design and implement extraordinary web solutions to help our clients achieve their goals.</p>
        <h2 class="heading">OUR FAITH...</h2>
        <p class="statement">We reflect the love of Christ in us and through us to our fellow employees, partners and clients.</p>
      </div>
    </article>
    <article class="board">
      <svg class="board-frame" viewBox="0 0 220 330" preserveAspectRatio="none" aria-hidden="true">
        <path d="M0 0H220V48C150 18 70 18 0 48Z" fill="var(--blue-deep)"/>
        <path d="M0 18C70 4 150 4 220 22V36C150 14 70 14 0 34Z" fill="var(--blue-soft)" opacity=".7"/>
        <path d="M0 54C70 24 150 24 220 54" fill="none" stroke="var(--silver)" stroke-width="7"/>
        <path d="M0 60C70 32 150 32 220 60" fill="none" stroke="var(--blue-pale)" stroke-width="2"/>
        <path d="M0 282C70 308 150 308 220 282V330H0Z" fill="var(--blue-deep)"/>
        <path d="M0 300C70 318 150 318 220 296V312C150 330 70 330 0 314Z" fill="var(--blue-soft)" opacity=".7"/>
        <path d="M0 276C70 302 150 302 220 276" fill="none" stroke="var(--silver)" stroke-width="7"/>
        <path d="M0 270C70 294 150 294 220 270" fill="none" stroke="var(--blue-pale)" stroke-width="2"/>
      </svg>
      <div class="board-content">
        <div class="brand"><span class="brand-dot"></span><span class="brand-name">TRELLISWORKS</span></div>
        <h2 class="heading values-heading">OUR CORE VALUES</h2>
        <p class="value"><span class="value-name">INTEGRITY</span>We believe that to be successful, it is essential to operate at the highest levels of honesty, responsibility and trust.</p>
        <p class="value"><span class="value-name">ACCOUNTABILITY</span>Taking responsibility for one's own actions.</p>
        <p class="value"><span class="value-name">RESPECT</span>Understand and value differences in others. Listen thoughtfully to understand.</p>
        <p class="value"><span class="value-name">EXCELLENCE</span>We continually improve our standards and processes so that excellence simply becomes a natural consequence of our work.</p>
        <p class="value"><span class="value-name">LOYALTY</span>Working collaboratively with TrellisWorks employees, partners and customers to solve problems and achieve goals.</p>
      </div>
    </article>
  </section>

</main>
</body>
</html>
```